Web Design Project

Psychotherapy and Counselling Practice needs a landing page web design.

My business "Larkfield Advisory" specialises in the treatment of Anxiety and Depression with a holistic approach, endeavouring to unlock the key that holds us to ransom in a life that is imbalanced, frustrating, and ultimately of our own making due to our own perceptions and behaviours.

There is much that impacts us which we cannot change, but we are always in control of how we think, and how we frame our experiences.....learning to challenge those thoughts and behaviours that are destructive and disempowering opens up a world of joyful possibility. Life is about making choices, learn to make wiser and healthier choices.......

Larkfield Advisory has a client base of individual clients but will seek to expand to offer services to the Corporate world by offering an adjunct to employers for established "Wellness Programs".

Larkfield Advisory is a highly professional, ethically bound business, with the needs of the client at the forefront of all we do.

Larkfield Advisory wishes to avoid the usual "jargon driven" psychobabble offered on many counselling web pages. It aims to be stylishly presented, clean in look and with as few "words" as possible and a largely white background (faster loading and more powerful impact of what is stated), those words contained in the webpage should be meaningful, persuasive and have an impact simply at glance. Larkfield does not want , or expect, those prospective clients in need of support , to be reading through volumes of industry driven cliches.

At this point Larkfield is just looking for a high quality landing page. However in time this will likely expand to include other sections such as case studies, video content etc.

Target Market(s)

Those in need of emotional support, suffering mental health issues, and those simply wanting to become self aware supported by a mindful therapist.

Industry/Entity Type

Industry

Requirements
Must have
• The design must incorporate the Larkfield logo and colour schemes found on the attached files.

```html
<!DOCTYPE html>
<html lang="en">
<head>
<meta charset="utf-8">
<title>Larkfield Advisory</title>
<link rel="stylesheet" href="https://fonts.googleapis.com/css2?family=Roboto:wght@300;400;500&display=swap">
<style>
  :root {
    --header-grey: #6a6a6a;
    --green: #a5bb45;
    --green-deep: #86a52c;
    --circle-green: #a9c04d;
    --white: #ffffff;
    --body-text: #7c7c7c;
    --heading-dark: #333333;
    --footer-bg: #e8e8e3;
    --client-dark: #2f2f2f;
  }
  * { box-sizing: border-box; margin: 0; padding: 0; }
  html, body { width: 1200px; height: 1000px; overflow: hidden; }
  body {
    position: relative;
    background: var(--white);
    font-family: "Roboto", Arial, sans-serif;
    color: var(--body-text);
  }
  .site-header {
    position: absolute; left: 0; top: 0; width: 1200px; height: 106px;
    background: var(--header-grey);
  }
  .brand-name {
    position: absolute; left: 126px; top: 30px;
    font-size: 38px; font-weight: 300; color: var(--white); letter-spacing: -1px;
  }
  .brand-mark {
    position: absolute; left: 500px; top: 50px;
    font-size: 16px; font-weight: 300; color: var(--green); letter-spacing: 0.5px;
  }
  .main-nav { position: absolute; top: 50px; left: 0; }
  .main-nav a {
    position: absolute; color: var(--white); text-decoration: none;
    font-size: 14px; white-space: nowrap;
  }
  .hero-band { position: absolute; left: 0; top: 112px; }
  .service {
    position: absolute; top: 188px; width: 219px; height: 402px;
  }
  .service-shadow {
    position: absolute; right: 0; top: 110px; width: 20px; height: 290px;
    background: linear-gradient(to right, rgba(0,0,0,0.14), rgba(0,0,0,0));
    transform: translateX(20px);
    border-radius: 0 0 20px 0;
  }
  .service-shadow::before {
    content: ""; position: absolute; left: -20px; top: 0; width: 20px; height: 100%;
    background: var(--white);
  }
  .service-circle {
    position: absolute; left: 0; top: 0; width: 205px; height: 205px;
    border-radius: 50%; background: var(--circle-green);
    border: 6px solid var(--white);
    display: flex; align-items: center; justify-content: center; text-align: center;
    color: var(--white); font-weight: 300; font-size: 30px; line-height: 36px;
    letter-spacing: -0.5px;
  }
  .service-text {
    position: absolute; left: 0; top: 228px; width: 204px;
    font-size: 12px; line-height: 18px; text-align: justify;
  }
  .site-footer {
    position: absolute; left: 0; top: 640px; width: 1200px; height: 360px;
    background-color: var(--footer-bg);
    background-image: radial-gradient(circle, rgba(0,0,0,0.08) 1px, transparent 1.5px);
    background-size: 24px 24px;
  }
  .about-title {
    position: absolute; left: 129px; top: 24px;
    font-size: 14px; color: var(--heading-dark);
  }
  .about-text {
    position: absolute; left: 129px; top: 50px; width: 440px;
    font-size: 12.4px; line-height: 18px; text-align: justify; color: #888;
  }
  .newsletter {
    position: absolute; left: 620px; top: 54px; width: 448px; height: 54px;
    background: var(--white); border-radius: 4px;
    box-shadow: inset 0 2px 4px rgba(0,0,0,0.15), 0 0 0 1px #dcdcd6;
  }
  .newsletter-icon { position: absolute; left: 21px; top: 20px; }
  .newsletter-placeholder {
    position: absolute; left: 48px; top: 20px; font-size: 12px; color: #999;
  }
  .newsletter-join {
    position: absolute; right: 7px; top: 9px; width: 58px; height: 38px;
    border-radius: 3px; border: 1px solid #6d8a22;
    background: linear-gradient(#9cbf3b, var(--green-deep));
    color: #3d4d14; font-size: 14px; font-weight: 500;
    display: flex; align-items: center; justify-content: center;
  }
  .clients-title {
    position: absolute; left: 620px; top: 171px; font-size: 14px; color: var(--heading-dark);
  }
  .client-list { position: absolute; left: 620px; top: 200px; width: 450px; height: 46px; }
  .client-name {
    position: absolute; top: 10px; font-size: 20px; font-weight: 500;
    color: var(--client-dark); white-space: nowrap;
  }
  .social-links { position: absolute; left: 483px; top: 301px; }
  .social-link {
    position: absolute; top: 0; width: 36px; height: 36px; border-radius: 50%;
    background: var(--green-deep);
    box-shadow: 3px 3px 0 rgba(0,0,0,0.25);
  }
</style>
</head>
<body>
  <header class="site-header">
    <div class="brand-name">Larkfield Advisory</div>
    <div class="brand-mark">LARKFIELD</div>
    <nav class="main-nav">
      <a href="#" style="left:738px">HOME</a>
      <a href="#" style="left:817px">ABOUT</a>
      <a href="#" style="left:902px">CONTACT</a>
      <a href="#" style="left:1004px">SERVICES</a>
    </nav>
  </header>

  <svg class="hero-band" width="1200" height="184" viewBox="0 0 1200 184" role="img" aria-label="Green band with soft geometric texture">
    <defs>
      <pattern id="teeth-top" width="10" height="8" patternUnits="userSpaceOnUse">
        <polygon points="0,8 5,2 10,8" fill="#a5bb45"/>
      </pattern>
      <pattern id="teeth-bottom" width="10" height="8" patternUnits="userSpaceOnUse">
        <polygon points="0,0 5,6 10,0" fill="#a5bb45"/>
      </pattern>
    </defs>
    <rect x="0" y="0" width="1200" height="8" fill="url(#teeth-top)"/>
    <rect x="0" y="8" width="1200" height="168" fill="#a5bb45"/>
    <rect x="0" y="176" width="1200" height="8" fill="url(#teeth-bottom)"/>
  </svg>

  <section class="service" style="left:128px">
    <div class="service-shadow"></div>
    <div class="service-circle">Anxiety</div>
    <p class="service-text">Lorem ipsum dolor sit amet, consectetur adipiscing elit. Mauris interdum velit vitae nulla molestie eu commodo nulla dapibus. Donec id sollicitudin urna. Integer at dui ac leo fermentum varius eleifend ut libero. Mauris interdum velit vitae nulla molestie eu commodo nulla dapibus.</p>
  </section>
  <section class="service" style="left:496px">
    <div class="service-shadow"></div>
    <div class="service-circle">Depression</div>
    <p class="service-text">Lorem ipsum dolor sit amet, consectetur adipiscing elit. Mauris interdum velit vitae nulla molestie eu commodo nulla dapibus. Donec id sollicitudin urna. Integer at dui ac leo fermentum varius eleifend ut libero. Mauris interdum velit vitae nulla molestie eu commodo nulla dapibus.</p>
  </section>
  <section class="service" style="left:864px">
    <div class="service-shadow"></div>
    <div class="service-circle">Wellness<br>program</div>
    <p class="service-text">Lorem ipsum dolor sit amet, consectetur adipiscing elit. Mauris interdum velit vitae nulla molestie eu commodo nulla dapibus. Donec id sollicitudin urna. Integer at dui ac leo fermentum varius eleifend ut libero. Mauris interdum velit vitae nulla molestie eu commodo nulla dapibus.</p>
  </section>

  <footer class="site-footer">
    <h2 class="about-title" style="font-weight:400">Lorem</h2>
    <p class="about-text">Lorem ipsum dolor sit amet, consectetur adipiscing elit. Mauris interdum velit vitae nulla molestie eu commodo nulla dapibus. Donec id sollicitudin urna. Integer at dui ac leo fermentum varius eleifend ut libero. Mauris interdum velit vitae nulla molestie eu commodo nulla dapibus.<br>Lorem ipsum dolor sit amet, consectetur adipiscing elit. Mauris interdum velit vitae nulla molestie eu commodo nulla dapibus. Donec id sollicitudin urna. Integer at dui ac leo fermentum varius eleifend ut libero. Mauris interdum velit vitae nulla molestie eu commodo nulla dapibus. Lorem ipsum dolor sit amet, consectetur adipiscing elit. Mauris interdum velit vitae nulla molestie eu commodo nulla dapibus. Donec id sollicitudin urna. Integer at dui ac leo fermentum varius eleifend ut libero. Mauris interdum velit vitae nulla molestie eu commodo nulla dapibus.</p>

    <div class="newsletter">
      <svg class="newsletter-icon" width="14" height="11" viewBox="0 0 14 11" aria-hidden="true">
        <rect x="0" y="0" width="14" height="11" rx="1" fill="#c8c8c8"/>
        <polyline points="0.5,0.8 7,6 13.5,0.8" fill="none" stroke="#ffffff" stroke-width="1.2"/>
      </svg>
      <span class="newsletter-placeholder">Join Our Newsletter Here</span>
      <span class="newsletter-join">Join</span>
    </div>

    <h3 class="clients-title" style="font-weight:400">Our corporate clients</h3>
    <div class="client-list">
      <span class="client-name" style="left:0">Norvale</span>
      <span class="client-name" style="left:92px">Kestrel Media</span>
      <span class="client-name" style="left:248px">Quantix</span>
      <span class="client-name" style="left:340px">Meridex</span>
    </div>

    <nav class="social-links" aria-label="Social links">
      <a class="social-link" href="#" style="left:0" aria-label="Social profile one"></a>
      <a class="social-link" href="#" style="left:49px" aria-label="News feed"></a>
      <a class="social-link" href="#" style="left:98px" aria-label="Social profile two"></a>
      <a class="social-link" href="#" style="left:147px" aria-label="Social profile three"></a>
      <a class="social-link" href="#" style="left:196px" aria-label="Social profile four"></a>
    </nav>
  </footer>
</body>
</html>
```